4th Generation Family Business Needs a New Card Design!

We are a family owned 4th Generation company. We are based in the Sydney, Australia area and we are desperately in need of a more modern and classy card. We are monumental masons who design, supply & erect lasting memorials throughout cemeteries in Sydney. Our customers are normally in a period of grieving. I have attached logo files that will need to be implemented on the card. Company was established 1935. Australian Owned and Operated. Card needs to be designed to PIXO.com specification.

Target Market(s)

Our target market is based upon people that a grieving for family members that have passed away. We also deal with alot of companies that own and operate cemeteries.

Industry/Entity Type

Business

Contact Information for Business Card

Simon Harcourt, Operations Manager, 0417293086, simon@harcourtmemorials.com.au
Lewis Harcourt, Director, 0491630572, lewis@harcourtmemorials.com.au
Phone # 02 9561 3048
Website: www.harcourtmemorials.com.au
Address: Suite 17, 8 Palfrey Lane, West Carlow, Sydney NSW 2156

Font styles to use
Serif
Decorative
Script

Requirements
Must have
• Would like to see the logo nicely implemented with a modern design. Embossed lettering would be a nice additive.

```html
<!DOCTYPE html>
<html lang="en">
<head>
<meta charset="utf-8">
<title>Harcourt Memorials – Business Card</title>
<link href="https://fonts.googleapis.com/css2?family=Cinzel:wght@500&family=Arimo:wght@400;700&display=swap" rel="stylesheet">
<style>
  :root {
    --bg: #3a3a3a;
    --gold: #f0c12f;
    --ink: #1f1d1d;
    --charcoal: #2a292a;
    --paper: #ffffff;
    --light: #f2f2f2;
  }
  * { box-sizing: border-box; margin: 0; padding: 0; }
  html, body { width: 1200px; height: 950px; overflow: hidden; }
  body {
    background: radial-gradient(ellipse at 50% 45%, #5a5a5a 0%, var(--bg) 70%);
    font-family: "Arimo", Arial, sans-serif;
    position: relative;
  }
  .card {
    position: absolute;
    left: 250px;
    width: 700px;
    height: 400px;
    box-shadow: 0 14px 30px rgba(0,0,0,.45);
    overflow: hidden;
  }
  .card--front { top: 50px; background: var(--gold); }
  .card--back { top: 500px; background: var(--paper); display: flex; }

  .brand {
    font-family: "Cinzel", Georgia, serif;
    font-weight: 500;
    color: var(--ink);
    text-align: center;
    line-height: 1.05;
    letter-spacing: 1px;
  }
  .card--front .brand {
    position: absolute;
    top: 118px; left: 0; right: 0;
    font-size: 46px;
  }
  .front-web {
    position: absolute;
    top: 300px; left: 0; right: 0;
    text-align: center;
    font-size: 15px;
    color: var(--ink);
  }

  .back-brand-side {
    width: 315px;
    display: flex;
    align-items: center;
    justify-content: center;
  }
  .back-brand-side .brand { font-size: 40px; }

  .contact-panel {
    position: relative;
    flex: 1;
    background: var(--charcoal);
    border-left: 3px solid var(--gold);
    padding: 54px 0 0 58px;
    color: var(--light);
  }
  .panel-notch {
    position: absolute;
    left: -14px; top: 82px;
    width: 16px; height: 30px;
  }
  .person-name { color: var(--gold); font-weight: 700; font-size: 22px; }
  .person-role { font-size: 16px; margin-top: 6px; }
  .address { font-size: 16px; line-height: 1.4; margin-top: 32px; }
  .contact-list { list-style: none; margin-top: 16px; }
  .contact-list li {
    display: flex; align-items: center; gap: 10px;
    font-size: 16px; line-height: 1.55;
  }
  .contact-list svg { width: 16px; height: 16px; flex: none; fill: var(--gold); }
</style>
</head>
<body>

<section class="card card--front" aria-label="Card front">
  <div class="brand">Harcourt<br>Memorials</div>
  <div class="front-web">www.harcourtmemorials.com.au</div>
</section>

<section class="card card--back" aria-label="Card back">
  <div class="back-brand-side">
    <div class="brand">Harcourt<br>Memorials</div>
  </div>
  <div class="contact-panel">
    <svg class="panel-notch" viewBox="0 0 16 30" aria-hidden="true">
      <path d="M16 0 L2 15 L16 30" fill="#2a292a" stroke="#f0c12f" stroke-width="3"/>
    </svg>
    <div class="person-name">Simon Harcourt</div>
    <div class="person-role">Operations Manager</div>
    <div class="address">Suite 17, 8 Palfrey Lane<br>West Carlow, Sydney NSW 2156</div>
    <ul class="contact-list">
      <li><svg viewBox="0 0 16 16" aria-hidden="true"><path d="M2 5c0-2 2-3 3-3l1 3-2 1c1 2 3 4 6 5l1-2 3 1c0 1-1 3-3 3C6 13 2 9 2 5z"/></svg>02 9561 3048</li>
      <li><svg viewBox="0 0 16 16" aria-hidden="true"><path d="M4 1h8v14H4zM5.5 3v9h5V3z"/></svg>0417293086</li>
      <li><svg viewBox="0 0 16 16" aria-hidden="true"><path d="M1 3h14v10H1zM2.5 4.5 8 9l5.5-4.5z"/></svg>simon@harcourtmemorials.com.au</li>
      <li><svg viewBox="0 0 16 16" aria-hidden="true"><circle cx="8" cy="8" r="7"/></svg>www.harcourtmemorials.com.au</li>
    </ul>
  </div>
</section>

</body>
</html>
```